Real Estate Wordpress Landing Page

I'm looking to a landing page dedicated to my real estate brokerage that's catered to promoting that my company provides 1.5% listings to home sellers... I have a couple examples that I'm really looking towards mocking in a version with similar color schemes using my current company colors/website.

http://harbelo.com/
https://www.quarvantis.com/about/one-percent-listing-fee

My brokerage company website is http://www.brightmarrow.us/

Target Market(s)

real estate home sellers & buyers

Industry/Entity Type

Real Estate

Coding

Coded - Design and coding required

Number of Pages Required

1 page

Colors
3176b5
0255a3
eaf1f7
cedeed

Requirements
Must have
• Company website colors - http://www.brightmarrow.us/
• Something around the lines of this website page - http://harbelo.com/
• Wordpress compatibility

```html
<!DOCTYPE html>
<html lang="en">
<head>
<meta charset="utf-8">
<title>Bright Marrow Realty – 1.5% Listings</title>
<link href="https://fonts.googleapis.com/css2?family=Montserrat:wght@400;500;600;700&display=swap" rel="stylesheet">
<style>
:root{
  --blue:#3176b5;
  --blue-deep:#0255a3;
  --ice:#eaf1f7;
  --mist:#cedeed;
  --red:#d0161b;
  --ink:#1c1c1c;
  --muted:#6b6b6b;
  --card:#f6f5f1;
  --footer:#353535;
  --footer-bar:#262626;
  --rule:#d9d9d9;
}
*{box-sizing:border-box;margin:0;padding:0}
html,body{width:1200px;height:3147px;overflow:hidden}
body{font-family:"Montserrat",Arial,sans-serif;color:var(--ink);background:#fff}
.page{width:1200px;height:3147px;display:flex;flex-direction:column}
.wrap{width:900px;margin:0 auto}

/* header */
.site-header{height:120px;background:linear-gradient(180deg,#fff 0%,#f3f6f9 100%);border-bottom:4px solid var(--blue)}
.site-header .wrap{height:100%;display:flex;align-items:center;justify-content:space-between;width:1000px}
.brand{display:flex;align-items:center;gap:12px}
.brand-mark{width:34px;height:34px;background:var(--blue-deep)}
.brand-name{font-weight:700;font-size:22px;color:var(--blue-deep);white-space:nowrap}
.header-actions{display:flex;align-items:center;gap:12px}
.phone{display:flex;align-items:center;gap:10px;margin-right:20px}
.phone-icon{width:34px;height:34px;background:var(--blue);display:flex;align-items:center;justify-content:center}
.phone-number{font-weight:700;font-size:18px;color:var(--blue-deep)}
.btn{display:inline-block;font-weight:700;font-size:13px;color:#fff;text-transform:uppercase;padding:12px 22px;letter-spacing:.5px;white-space:nowrap}
.btn-red{background:var(--red)}
.btn-blue{background:var(--blue)}

/* hero */
.hero{height:680px;background:linear-gradient(160deg,#e9ece8 0%,#c9d2c6 35%,#5f8f4a 65%,#2f5a2a 100%)}

/* intro */
.intro{height:390px;background:var(--ice);text-align:center;padding-top:62px}
.section-title{font-weight:700;font-size:28px;color:var(--blue-deep);white-space:nowrap}
.section-title.dark{color:var(--ink)}
.intro-sub{font-weight:600;font-size:18px;margin-top:14px}
.lead-form{width:900px;margin:50px auto 0;display:grid;grid-template-columns:repeat(3,1fr);gap:18px 22px}
.field{height:42px;background:#fff;border:1px solid var(--mist);font-size:13px;color:#888;display:flex;align-items:center;justify-content:space-between;padding:0 14px;text-align:left}
.lead-form .btn{height:42px;display:flex;align-items:center;justify-content:center;font-size:10.5px;padding:0;letter-spacing:.2px}

/* listings */
.latest{height:520px;text-align:center;padding-top:62px}
.section-sub{font-weight:500;font-size:15px;color:var(--blue);margin-top:14px;white-space:nowrap}
.cards{width:900px;margin:44px auto 0;display:grid;grid-template-columns:repeat(3,1fr);gap:36px;text-align:left}
.photo{height:170px}
.photo.house{background:linear-gradient(170deg,#9cc2e6 0%,#e7e1cf 45%,#6d9a4c 100%)}
.photo.room{background:linear-gradient(170deg,#f0f0ef 0%,#9a9c9e 55%,#3b3d40 100%)}
.photo.villa{background:linear-gradient(170deg,#a9d0ec 0%,#efe6c6 50%,#6f9b52 100%)}
.listing-meta{display:flex;justify-content:space-between;align-items:flex-start;gap:8px;margin-top:12px}
.listing-addr{font-weight:700;font-size:14px;white-space:nowrap}
.listing-city{font-size:12px;color:var(--muted);margin-top:4px}
.listing-price{font-weight:700;font-size:13px;color:var(--blue-deep);white-space:nowrap}
.divider{width:900px;margin:56px auto 0;height:5px;background:var(--rule)}

/* guarantee */
.guarantee{height:847px;text-align:center;padding-top:70px}
.offer{background:var(--card);text-align:left}
.offer .photo{height:200px}
.offer-body{padding:18px 16px 20px}
.offer-addr{font-size:12px;font-weight:600;color:var(--blue);white-space:nowrap}
.offer-title{font-size:12.5px;font-weight:700;margin-top:10px;white-space:nowrap}
.offer-price{font-size:24px;font-weight:500;color:var(--blue);margin-top:10px}
.offer-list{list-style:none;margin-top:14px;font-size:11.5px;line-height:1.7;color:#333;white-space:nowrap}
.offer-call{display:block;background:var(--blue);color:#fff;text-align:center;font-weight:700;font-size:14px;padding:12px 0;letter-spacing:.5px}

/* broker */
.broker{height:400px;background:linear-gradient(180deg,#f1f2f3 0%,#e4e6e8 100%);position:relative}
.broker-art{position:absolute;left:90px;top:20px;width:280px;height:360px;background:linear-gradient(160deg,#7fbf9a 0%,#3c8f6a 60%,#e5e5e5 100%)}
.broker-text{position:absolute;left:390px;top:90px;width:640px;text-align:center}
.broker-name{font-weight:700;font-size:27px;letter-spacing:1px;white-space:nowrap}
.broker-copy{font-size:15px;line-height:1.6;margin-top:22px}
.broker-text .btn{margin-top:26px;background:var(--blue-deep)}

/* footer */
.site-footer{height:150px;background:var(--footer)}
.site-footer .wrap{width:1000px;height:100%;display:flex;align-items:center;justify-content:space-between}
.site-footer .brand-name{color:#fff;font-size:20px}
.site-footer .brand-mark{background:var(--blue)}
.footer-copy{width:500px;font-size:14px;line-height:1.6;color:#ddd}
.footer-copy .hl{color:var(--blue)}
.social{display:flex;gap:10px}
.social span{width:30px;height:30px;border:1px solid #888}
.copyright{height:40px;background:var(--footer-bar);color:#999;font-size:11px;display:flex;align-items:center;justify-content:center}
</style>
</head>
<body>
<div class="page">

  <header class="site-header">
    <div class="wrap">
      <div class="brand"><span class="brand-mark"></span><span class="brand-name">Bright Marrow Realty</span></div>
      <div class="header-actions">
        <div class="phone">
          <span class="phone-icon"><svg width="18" height="18" viewBox="0 0 24 24"><path fill="#fff" d="M6.6 10.8a15.1 15.1 0 0 0 6.6 6.6l2.2-2.2a1 1 0 0 1 1-.25 11.4 11.4 0 0 0 3.6.57 1 1 0 0 1 1 1V20a1 1 0 0 1-1 1A17 17 0 0 1 3 4a1 1 0 0 1 1-1h3.5a1 1 0 0 1 1 1c0 1.25.2 2.45.57 3.6a1 1 0 0 1-.25 1z"/></svg></span>
          <span class="phone-number">555-482-1067</span>
        </div>
        <span class="btn btn-red">Buy with us</span>
        <span class="btn btn-blue">Sell with us</span>
      </div>
    </div>
  </header>

  <section class="hero" role="img" aria-label="Photo of a white home entrance framed by tropical plants with a for-sale sign on the path"></section>

  <section class="intro">
    <h1 class="section-title">– Changing the Way Real Estate is Sold and Purchased. –</h1>
    <p class="intro-sub">List for only 1.5% | Get 1% Back when you Purchase</p>
    <div class="lead-form">
      <div class="field">Name*</div>
      <div class="field">Email*</div>
      <div class="field">Phone Number*</div>
      <div class="field">Interested In <span>▾</span></div>
      <div class="field">Interested In</div>
      <span class="btn btn-red">Contact Bright Marrow and save today!</span>
    </div>
  </section>

  <section class="latest">
    <h2 class="section-title dark">– Latest Properties –</h2>
    <p class="section-sub">List For 1.5% Commission, And Receive Top Marketing from Real Estate Pro!</p>
    <div class="cards">
      <article>
        <div class="photo house" role="img" aria-label="Two-storey house with garage"></div>
        <div class="listing-meta"><div><div class="listing-addr">412 Fernbrook Cove Lane</div><div class="listing-city">Lake Worth, FL 33463</div></div><div class="listing-price">$310,000</div></div>
      </article>
      <article>
        <div class="photo room" role="img" aria-label="Bright modern living room"></div>
        <div class="listing-meta"><div><div class="listing-addr">218 Palmetta Boulevard,</div><div class="listing-city">202 Boynton Beach, FL 33435</div></div><div class="listing-price">$499,000</div></div>
      </article>
      <article>
        <div class="photo villa" role="img" aria-label="Cream house with palm trees"></div>
        <div class="listing-meta"><div><div class="listing-addr">7731 Cedar Mill Circle</div><div class="listing-city">Lake Worth, FL 33449</div></div><div class="listing-price">$310,000</div></div>
      </article>
    </div>
    <div class="divider"></div>
  </section>

  <section class="guarantee">
    <h2 class="section-title dark">– 30 Day Listing Service GUARANTEED. –</h2>
    <p class="section-sub">Save thousands $$$ listing with us! Morbi eu sem felis. Integer faucibus ligula vitae enim vestibulum iaculis.</p>
    <div class="cards">
      <article class="offer">
        <div class="photo house" role="img" aria-label="Two-storey house with garage"></div>
        <div class="offer-body">
          <div class="offer-addr">309 Harbor Glen Drive, FL 33462</div>
          <div class="offer-title">SELL WITH BRIGHT MARROW &amp; SAVE $$$</div>
          <div class="offer-price">$310,000</div>
          <ul class="offer-list"><li>Professional Real Estate Photography</li><li>Comparative Market Analysis (CMA)</li><li>FREE Consultation with Real Estate Pro</li></ul>
        </div>
        <span class="offer-call">CALL US : 555-318-2754</span>
      </article>
      <article class="offer">
        <div class="photo room" role="img" aria-label="Bright modern living room"></div>
        <div class="offer-body">
          <div class="offer-addr">309 Harbor Glen Drive, FL 33462</div>
          <div class="offer-title">SELL WITH BRIGHT MARROW &amp; SAVE $$$</div>
          <div class="offer-price">$310,000</div>
          <ul class="offer-list"><li>Professional Real Estate Photography</li><li>Comparative Market Analysis (CMA)</li><li>FREE Consultation with Real Estate Pro</li></ul>
        </div>
        <span class="offer-call">CALL US : 555-318-2754</span>
      </article>
      <article class="offer">
        <div class="photo villa" role="img" aria-label="Cream house with palm trees"></div>
        <div class="offer-body">
          <div class="offer-addr">309 Harbor Glen Drive, FL 33462</div>
          <div class="offer-title">SELL WITH BRIGHT MARROW &amp; SAVE $$$</div>
          <div class="offer-price">$310,000</div>
          <ul class="offer-list"><li>Professional Real Estate Photography</li><li>Comparative Market Analysis (CMA)</li><li>FREE Consultation with Real Estate Pro</li></ul>
        </div>
        <span class="offer-call">CALL US : 555-318-2754</span>
      </article>
    </div>
  </section>

  <section class="broker">
    <div class="broker-art" role="img" aria-label="Illustration of a hand holding a green house with keys"></div>
    <div class="broker-text">
      <h2 class="broker-name">DAREN OSIMA, Lic. Real Estate Broker</h2>
      <p class="broker-copy">On average, our customers save $5,600 when they list with us... and they still receive top marketing and quality professional service!</p>
      <span class="btn">Contact Bright Marrow and save today!</span>
    </div>
  </section>

  <footer>
    <div class="site-footer">
      <div class="wrap">
        <div class="brand"><span class="brand-mark"></span><span class="brand-name">Bright Marrow</span></div>
        <p class="footer-copy"><span class="hl">30 Day</span> Listing Service <span class="hl">GUARANTEED</span>. Save thousands $$$ listing with us! Morbi eu sem felis. Integer faucibus ligula vitae enim vestibulum iaculis.</p>
        <div class="social"><span></span><span></span><span></span><span></span><span></span></div>
      </div>
    </div>
    <div class="copyright">Copyright © 2018 Bright Marrow Realty. All Rights Reserved.</div>
  </footer>

</div>
</body>
</html>
```